Quote Cards With KB May 2025 for Instagram

I would like to put these quotes over one of the pictures attached; Instagram (new size: 4:5 (1080 x 1350 pixels) One Quote per picture, and I want the quote to be bold or easy to read as well. I provided a few reference graphics that I really like as examples below. In very small letters at the bottom add @KBHarlowOnline

All of the pictures are attached; you can pick any photo and add one quote to it; but no stock photography

```html
<!DOCTYPE html>
<html lang="en">
<head>
<meta charset="utf-8">
<title>Quote Cards With KB — May 2025</title>
<link rel="stylesheet" href="https://fonts.googleapis.com/css2?family=Oswald:wght@600&family=Outfit:wght@600;700&display=swap">
<style>
  :root {
    --board: #a2a2a2;
    --card-top: #fff6fb;
    --card-bottom: #ffd0e8;
    --ring: #f7a3cf;
    --headline: #c8116b;
    --body: #1b1b1b;
    --handle: #c8116b;
    --photo-a: #5a4a4c;
    --photo-b: #2a2224;
  }
  * { margin: 0; padding: 0; box-sizing: border-box; }
  html, body { width: 1200px; height: 3217px; overflow: hidden; }
  body { background: var(--board); position: relative; }

  .quote-card {
    position: absolute;
    width: 461px;
    height: 576px;
    overflow: hidden;
    background: linear-gradient(180deg, var(--card-top) 0%, var(--card-bottom) 100%);
  }
  .col-left { left: 120px; }
  .col-right { left: 619px; }
  .row-1 { top: 81px; }
  .row-2 { top: 692px; }
  .row-3 { top: 1307px; }
  .row-4 { top: 1929px; }
  .row-5 { top: 2560px; }

  .photo-frame { position: absolute; inset: 0; width: 461px; height: 576px; }

  .headline {
    position: absolute;
    left: 24px;
    font-family: "Oswald", "Arial Narrow", sans-serif;
    font-weight: 600;
    color: var(--headline);
    letter-spacing: -0.02em;
    transform: scaleX(0.86);
    transform-origin: left top;
  }
  .body-copy {
    position: absolute;
    left: 28px;
    font-family: "Outfit", "Helvetica", sans-serif;
    font-weight: 600;
    color: var(--body);
  }
  .body-copy strong { font-weight: 700; letter-spacing: 0.01em; }
  .handle {
    position: absolute;
    left: 28px;
    top: 533px;
    font-family: "Outfit", "Helvetica", sans-serif;
    font-weight: 600;
    font-size: 15px;
    color: var(--handle);
  }
</style>
</head>
<body>
<svg width="0" height="0" style="position:absolute">
  <defs>
    <linearGradient id="photo-tone" x1="0" y1="0" x2="0" y2="1">
      <stop offset="0" stop-color="#7a6a6c"/>
      <stop offset="1" stop-color="#2a2224"/>
    </linearGradient>
    <linearGradient id="photo-pink" x1="0" y1="0" x2="1" y2="1">
      <stop offset="0" stop-color="#5a3f9a"/>
      <stop offset="1" stop-color="#d8308f"/>
    </linearGradient>
    <linearGradient id="photo-court" x1="0" y1="0" x2="0" y2="1">
      <stop offset="0" stop-color="#4a4652"/>
      <stop offset="1" stop-color="#b88a4a"/>
    </linearGradient>
    <linearGradient id="photo-outdoor" x1="0" y1="0" x2="0" y2="1">
      <stop offset="0" stop-color="#b9d6ea"/>
      <stop offset="1" stop-color="#3c4a36"/>
    </linearGradient>
    <linearGradient id="photo-floral" x1="0" y1="0" x2="0" y2="1">
      <stop offset="0" stop-color="#9aa3a8"/>
      <stop offset="1" stop-color="#c77f8e"/>
    </linearGradient>
  </defs>
</svg>

<!-- Card 1 -->
<section class="quote-card col-left row-1">
  <svg class="photo-frame" viewBox="0 0 461 576">
    <ellipse cx="480" cy="190" rx="265" ry="285" fill="var(--ring)"/>
    <ellipse cx="495" cy="190" rx="255" ry="280" fill="url(#photo-tone)" role="img" aria-label="Photo of KB in a sheer black striped top, pointing down, in a kitchen"/>
  </svg>
  <h2 class="headline" style="top:66px;font-size:58px;line-height:58px;">Tired.<br>Moody.<br>Stubborn<br>Belly Fat.</h2>
  <p class="body-copy" style="top:342px;font-size:28px;line-height:36px;">Your hormones<br>are screaming<br>for help!<br>Let’s fix that.</p>
  <p class="handle">@KBHarlowOnline</p>
</section>

<!-- Card 2 -->
<section class="quote-card col-right row-1">
  <svg class="photo-frame" viewBox="0 0 461 576">
    <ellipse cx="560" cy="300" rx="348" ry="440" fill="var(--ring)"/>
    <ellipse cx="575" cy="300" rx="335" ry="440" fill="url(#photo-pink)" role="img" aria-label="Photo of KB in a long magenta gown at an awards stage"/>
  </svg>
  <h2 class="headline" style="top:62px;font-size:48px;line-height:52px;">That stubborn<br>weight?<br>It’s not your<br>fault.</h2>
  <p class="body-copy" style="left:23px;top:286px;font-size:26px;line-height:32px;">Your hormones<br>are to blame and<br>you’re not alone;<br>But there is a fix.</p>
  <p class="handle" style="left:20px;">@KBHarlowOnline</p>
</section>

<!-- Card 3 -->
<section class="quote-card col-left row-2">
  <svg class="photo-frame" viewBox="0 0 461 576">
    <ellipse cx="520" cy="195" rx="290" ry="285" fill="var(--ring)"/>
    <ellipse cx="535" cy="195" rx="278" ry="280" fill="url(#photo-tone)" role="img" aria-label="Photo of KB in a white cropped sweater, pointing up"/>
  </svg>
  <h2 class="headline" style="left:18px;top:60px;font-size:46px;line-height:47px;">Your belly<br>isn’t fat…<br>it’s hormonal.<br>And here’s<br>how to fix it.</h2>
  <p class="body-copy" style="left:18px;top:330px;font-size:30px;line-height:38px;">Comment<br><strong>HORMONES</strong><br>if nothing is<br>working.</p>
  <p class="handle" style="left:18px;top:528px;">@KBHarlowOnline</p>
</section>

<!-- Card 4 -->
<section class="quote-card col-right row-2">
  <svg class="photo-frame" viewBox="0 0 461 576">
    <ellipse cx="560" cy="270" rx="345" ry="440" fill="var(--ring)"/>
    <ellipse cx="575" cy="270" rx="333" ry="440" fill="url(#photo-court)" role="img" aria-label="Photo of KB in a sparkly brown top and black jeans on a basketball court"/>
  </svg>
  <h2 class="headline" style="left:20px;top:56px;font-size:42px;line-height:50px;">The stubborn<br><span style="font-size:58px;line-height:56px;">belly fat<br>after 40?</span></h2>
  <p class="body-copy" style="left:20px;top:262px;font-size:26px;line-height:32px;">It’s not about<br>calories;<br>it’s about your<br>hormones.<br>Here is the fix!</p>
  <p class="handle" style="left:20px;">@KBHarlowOnline</p>
</section>

<!-- Card 5 -->
<section class="quote-card col-left row-3">
  <svg class="photo-frame" viewBox="0 0 461 576">
    <ellipse cx="505" cy="235" rx="285" ry="350" fill="var(--ring)"/>
    <ellipse cx="520" cy="235" rx="272" ry="345" fill="url(#photo-outdoor)" role="img" aria-label="Photo of KB in a black top and jeans outdoors on a hillside"/>
  </svg>
  <h2 class="headline" style="left:20px;top:50px;font-size:50px;line-height:52px;">Flat tummy<br>in your 40s?</h2>
  <p class="body-copy" style="left:18px;top:196px;font-size:29px;line-height:37px;">It’s still<br>possible!<br>Comment<br><strong style="font-size:32px;">BYE BELLY</strong><br>to get the<br>10 secrets to<br>a flatter<br>tummy</p>
  <p class="handle" style="left:20px;">@KBHarlowOnline</p>
</section>

<!-- Card 6 -->
<section class="quote-card col-right row-3">
  <svg class="photo-frame" viewBox="0 0 461 576">
    <ellipse cx="545" cy="240" rx="335" ry="440" fill="var(--ring)"/>
    <ellipse cx="560" cy="240" rx="322" ry="440" fill="url(#photo-floral)" role="img" aria-label="Photo of KB in a sparkly pink outfit beside sunflowers"/>
  </svg>
  <h2 class="headline" style="left:20px;top:40px;font-size:58px;line-height:59px;">Bloating.<br>Muffin top.<br>Puffy<br>waistline.</h2>
  <p class="body-copy" style="left:20px;top:298px;font-size:27px;line-height:32px;">Your body’s<br>screaming for<br>a different<br>kind of fix.<br>Here it is</p>
  <p class="handle" style="left:20px;">@KBHarlowOnline</p>
</section>

<!-- Card 7 -->
<section class="quote-card col-left row-4">
  <svg class="photo-frame" viewBox="0 0 461 576">
    <ellipse cx="555" cy="280" rx="335" ry="440" fill="var(--ring)"/>
    <ellipse cx="570" cy="280" rx="322" ry="440" fill="url(#photo-tone)" role="img" aria-label="Photo of KB in a sheer black top blowing a kiss"/>
  </svg>
  <h2 class="headline" style="left:22px;top:60px;font-size:44px;line-height:45px;">You’re doing all<br>the “right”<br>things, but your<br>belly won’t go<br>down?</h2>
  <p class="body-copy" style="left:20px;top:356px;font-size:29px;line-height:35px;">Here’s what<br>you haven’t<br>tried.</p>
  <p class="handle" style="left:20px;">@KBHarlowOnline</p>
</section>

<!-- Card 8 -->
<section class="quote-card col-right row-4">
  <svg class="photo-frame" viewBox="0 0 461 576">
    <ellipse cx="535" cy="280" rx="315" ry="440" fill="var(--ring)"/>
    <ellipse cx="550" cy="280" rx="302" ry="440" fill="url(#photo-tone)" role="img" aria-label="Photo of KB in a sheer black top by a city-view window at night"/>
  </svg>
  <h2 class="headline" style="left:20px;top:34px;font-size:44px;line-height:47px;">This 90-day plan<br>helped women<br>over 40 slim<br>down,<br>get a tiny waist<br>and feel sexy<br>again.</h2>
  <p class="body-copy" style="left:20px;top:418px;font-size:31px;line-height:36px;">You’re next</p>
  <p class="handle" style="left:20px;">@KBHarlowOnline</p>
</section>

<!-- Card 9 -->
<section class="quote-card col-left row-5">
  <svg class="photo-frame" viewBox="0 0 461 576">
    <ellipse cx="510" cy="230" rx="305" ry="300" fill="var(--ring)"/>
    <ellipse cx="525" cy="230" rx="292" ry="295" fill="url(#photo-outdoor)" role="img" aria-label="Photo of KB in a black outfit against hills and blue sky"/>
  </svg>
  <h2 class="headline" style="left:24px;top:34px;font-size:38px;line-height:40px;">This is the<br>secret women<br>over 40are<br>using to get<br>snatched;<br>without<br>starving.</h2>
  <p class="body-copy" style="left:24px;top:340px;font-size:29px;line-height:36px;">Comment<br><strong style="font-size:36px;">SKINNY</strong><br>to get the<br>exact plan.</p>
  <p class="handle" style="left:24px;top:536px;">@KBHarlowOnline</p>
</section>

<!-- Card 10 -->
<section class="quote-card col-right row-5">
  <svg class="photo-frame" viewBox="0 0 461 576">
    <ellipse cx="500" cy="215" rx="285" ry="275" fill="var(--ring)"/>
    <ellipse cx="515" cy="215" rx="272" ry="270" fill="url(#photo-tone)" role="img" aria-label="Photo of KB from behind in a black open-back top"/>
  </svg>
  <h2 class="headline" style="left:22px;top:34px;font-size:47px;line-height:52px;">What worked<br>in your 30s<br>won’t work<br>now.<br>Here’s what<br>actually does.</h2>
  <p class="body-copy" style="left:26px;top:378px;font-size:27px;line-height:34px;">Drop 30 Pounds<br>in 3 Months.</p>
  <p class="handle" style="left:26px;top:530px;">@KBHarlowOnline</p>
</section>
</body>
</html>
```